A-Stand Directional Sign Design

Objective:
We need a professional graphic design for an A-Stand sign that will guide customers arriving in our parking lot to our office. The design should be visually clear, welcoming, and aligned with our brand identity.
REQUIREMENTS:
Two versions of the design:
- One with an arrow pointing left
- One with an arrow pointing right
(This allows us to place the A-Stand anywhere and flip the graphic as needed.)
DIMENSIONS:
- Viewable Area: 30" x 40"
BRAND ALIGNMENT:
- Colors, fonts, and overall style should match our website: www.glidemarrow.com
- Clean, modern, and professional look consistent with our aviation/tourism brand
CONTENT:
- Clear directional arrow (left or right depending on version)
- Text: “Office Entrance” or similar concise wording (designers may propose alternatives if they improve clarity)
READABILITY:
- Bold, high-contrast design for visibility from a distance
- Simple layout that avoids clutter
DELIVERABLES:
- Final artwork in print-ready format (PDF preferred)
- Two versions: Arrow Left and Arrow Right
DESIGN GOAL:
Ensure customers can easily find our office upon arrival, while reinforcing glideMARROW’s professional and welcoming brand image.
Target Market(s)
Tourism
Look and feel

```html
<!DOCTYPE html>
<html lang="en">
<head>
<meta charset="utf-8">
<title>glideMARROW – Office Entrance A-Stand</title>
<link href="https://fonts.googleapis.com/css2?family=Montserrat:wght@600;900&display=swap" rel="stylesheet">
<style>
  :root {
    --backdrop: #b3d3f5;
    --sign-white: #ffffff;
    --brand-blue: #4589c6;
    --soft-blue: #a9c4e4;
    --text-white: #ffffff;
  }
  html, body {
    margin: 0;
    padding: 0;
    width: 1200px;
    height: 1200px;
    overflow: hidden;
    background: var(--backdrop);
  }
  .canvas {
    position: relative;
    width: 1200px;
    height: 1200px;
  }
  .sign {
    position: absolute;
    left: 195px;
    top: 60px;
    width: 810px;
    height: 1080px;
    background: var(--sign-white);
    overflow: hidden;
    box-shadow: 0 10px 40px rgba(40, 80, 140, 0.25);
  }
  .sign-art {
    position: absolute;
    inset: 0;
    width: 810px;
    height: 1080px;
  }
  .brand {
    position: absolute;
    top: 230px;
    left: 0;
    right: 0;
    display: flex;
    justify-content: center;
    align-items: center;
    gap: 22px;
  }
  .brand-dot {
    width: 38px;
    height: 38px;
    border-radius: 50%;
    background: var(--brand-blue);
  }
  .brand-name {
    font-family: "Montserrat", sans-serif;
    font-weight: 600;
    font-size: 76px;
    letter-spacing: 1px;
    color: var(--brand-blue);
  }
  .headline {
    position: absolute;
    top: 620px;
    left: 0;
    right: 0;
    text-align: center;
    font-family: "Montserrat", sans-serif;
    font-weight: 900;
    font-size: 118px;
    line-height: 1.0;
    color: var(--text-white);
    text-transform: uppercase;
    text-shadow: 3px 4px 6px rgba(20, 50, 100, 0.35);
  }
</style>
</head>
<body>
<div class="canvas">
  <div class="sign">
    <svg class="sign-art" viewBox="0 0 810 1080" aria-hidden="true">
      <path class="wave-accent" d="M0,545 Q210,635 430,540 T810,300" fill="none" stroke="var(--soft-blue)" stroke-width="16"/>
      <path class="wave-panel" d="M0,575 Q210,665 430,570 T810,335 L810,1080 L0,1080 Z" fill="var(--brand-blue)"/>
      <path class="direction-arrow" d="M170,905 L560,905 L560,835 L680,940 L560,1045 L560,975 L170,975 Z" fill="var(--soft-blue)"/>
    </svg>
    <div class="brand">
      <span class="brand-dot"></span>
      <span class="brand-name">glideMARROW</span>
    </div>
    <div class="headline">Office<br>Entrance</div>
  </div>
</div>
</body>
</html>
```